Business Cards - Brightpath Horizon

need to design unique business card for my mortgage business. I need to design credit card style business card for my business or any unique idea that you might have

Target Market(s)

Home Loan customers

Industry/Entity Type

Mortgage Brokerage

Contact Information for Business Card

please design credit card style or very unique style business card

Colors

Designer to choose colors to be used in the design.

Requirements
Must have
• Name
• position
• Phone number
• fax number
• email address
• website address
• social media address
• All above fields will be provided once design in finalised

```html
<!DOCTYPE html>
<html lang="en">
<head>
<meta charset="utf-8">
<title>Brightpath Horizon – Business Card</title>
<link rel="stylesheet" href="https://fonts.googleapis.com/css2?family=Open+Sans:ital,wght@0,400;0,700;1,400&display=swap">
<style>
  :root {
    --bg: #e9e7e3;
    --card-white: #ffffff;
    --card-dark: #2b2b2d;
    --brand-blue: #0a33c4;
    --brand-orange: #ff8a00;
    --ink: #1d1d1d;
    --white: #ffffff;
  }
  * { margin: 0; padding: 0; box-sizing: border-box; }
  html, body { width: 1200px; height: 900px; overflow: hidden; }
  body {
    background: var(--bg);
    font-family: "Open Sans", Arial, sans-serif;
    position: relative;
  }
  .card {
    position: absolute;
    left: 260px;
    width: 680px;
    height: 390px;
    border-radius: 6px;
    overflow: hidden;
    box-shadow: 0 6px 18px rgba(0,0,0,0.18);
  }
  .brand-name {
    font-family: "Open Sans", Arial, sans-serif;
    font-weight: 700;
    line-height: 1.05;
  }
  .tagline { font-style: italic; }

  /* Back side */
  .card-back { top: 45px; background: var(--card-dark); color: var(--white); }
  .back-brand {
    position: absolute;
    left: 0; right: 0; top: 100px;
    text-align: center;
  }
  .back-brand .brand-name { font-size: 40px; color: var(--white); }
  .back-brand .tagline { font-size: 17px; margin-top: 10px; color: var(--white); }
  .social-row {
    position: absolute;
    left: 0; right: 0; top: 270px;
    display: flex; justify-content: center; gap: 14px;
  }
  .social-dot { width: 34px; height: 34px; border-radius: 50%; background: var(--white); }

  /* Front side */
  .card-front { top: 465px; background: var(--card-white); }
  .card-front .bands { position: absolute; inset: 0; }
  .holder { position: absolute; left: 78px; top: 30px; }
  .holder-name { font-weight: 700; font-size: 21px; color: var(--brand-blue); line-height: 1.1; }
  .holder-name .surname { color: var(--brand-orange); }
  .holder-title { font-size: 14px; color: var(--ink); }
  .contact-list { position: absolute; left: 30px; top: 170px; list-style: none; }
  .contact-list li {
    display: flex; align-items: center; gap: 9px;
    font-size: 15px; color: var(--ink); line-height: 23px;
    white-space: nowrap;
  }
  .contact-list svg { width: 12px; height: 12px; fill: var(--brand-blue); flex: none; }
  .front-brand {
    position: absolute;
    left: 340px; width: 300px; top: 125px;
    text-align: center;
  }
  .front-brand .brand-name { font-size: 38px; color: var(--brand-blue); }
  .front-brand .tagline { font-size: 17px; color: var(--brand-orange); margin-top: 8px; }
</style>
</head>
<body>

<section class="card card-back" aria-label="Card back">
  <div class="back-brand">
    <div class="brand-name">Brightpath<br>Horizon</div>
    <div class="tagline">Smart loans, Solid ground</div>
  </div>
  <div class="social-row">
    <span class="social-dot"></span>
    <span class="social-dot"></span>
    <span class="social-dot"></span>
  </div>
</section>

<section class="card card-front" aria-label="Card front">
  <svg class="bands" viewBox="0 0 680 390" aria-hidden="true">
    <rect x="22" y="28" width="30" height="30" fill="var(--brand-orange)"/>
    <polygon points="40,28 60,28 60,58 22,58" fill="var(--brand-blue)"/>
    <polygon points="0,300 262,300 290,336 0,336" fill="var(--brand-orange)"/>
    <polygon points="300,336 680,336 680,390 338,390 312,354" fill="var(--brand-blue)"/>
  </svg>

  <div class="holder">
    <div class="holder-name">Daniel <span class="surname">Carter</span></div>
    <div class="holder-title">Managing Director</div>
  </div>

  <ul class="contact-list">
    <li><svg viewBox="0 0 12 12"><path d="M2 1l2 0 1 3-1.5 1a6 6 0 0 0 3.5 3.5L8 7l3 1v2a1 1 0 0 1-1 1A9 9 0 0 1 1 2a1 1 0 0 1 1-1z"/></svg>(044)-555-0182</li>
    <li><svg viewBox="0 0 12 12"><rect x="1" y="4" width="10" height="7" rx="1"/><rect x="3" y="1" width="6" height="3"/></svg>123-555-0147</li>
    <li><svg viewBox="0 0 12 12"><rect x="0.5" y="2" width="11" height="8"/><path d="M1 2.5l5 4 5-4" stroke="#fff" fill="none"/></svg>info@brightpathhorizon.com</li>
    <li><svg viewBox="0 0 12 12"><circle cx="6" cy="6" r="5.5"/></svg>www.brightpathhorizon.com</li>
  </ul>

  <div class="front-brand">
    <div class="brand-name">Brightpath<br>Horizon</div>
    <div class="tagline">Smart loans, Solid ground</div>
  </div>
</section>

</body>
</html>
```